Alcohol brand needs design for gift tin packaging

We need a new design for the gift tins for our vodka brand. The bottles are in the shape of an oil barrel and the tins are also in the same shape. We would like to see the use of our logo. The gift tin needs to have a premium look.
Images of our bottles, logo and the gift tin are attached.

```html
<!DOCTYPE html>
<html lang="en">
<head>
<meta charset="utf-8">
<title>Iron Drum Vodka – Gift Tin Wrap</title>
<link href="https://fonts.googleapis.com/css2?family=Staatliches&display=swap" rel="stylesheet">
<style>
  :root {
    --backdrop: #d6d6d6;
    --tin-black: #0e0e0e;
    --tin-sheen: #3c3c3c;
    --copper: #c2521c;
    --copper-bright: #e8692a;
    --copper-deep: #7a2a0c;
    --grid-line: rgba(194, 82, 28, 0.7);
  }
  html, body {
    margin: 0;
    padding: 0;
    width: 1200px;
    height: 1170px;
    overflow: hidden;
    background: var(--backdrop);
  }
  .canvas {
    position: relative;
    width: 1200px;
    height: 1170px;
  }
  .tin-wrap {
    position: absolute;
    left: 60px;
    top: 60px;
    width: 1080px;
    height: 1050px;
    background: linear-gradient(90deg, var(--tin-black) 0%, var(--tin-sheen) 22%, var(--tin-black) 40%, var(--tin-sheen) 68%, var(--tin-black) 100%);
    overflow: hidden;
  }
  .wrap-art {
    position: absolute;
    inset: 0;
  }
  .label-text {
    position: absolute;
    font-family: "Staatliches", "Arial Narrow", sans-serif;
    color: var(--copper);
    line-height: 0.9;
    white-space: nowrap;
    transform-origin: left top;
  }
  .label-vodka { left: 70px; top: 250px; font-size: 96px; transform: rotate(-72deg); }
  .label-caution { left: 120px; top: 330px; font-size: 62px; transform: rotate(-48deg); letter-spacing: 4px; }
  .label-since { left: 600px; top: 120px; font-size: 64px; text-align: center; transform: rotate(-8deg); }
  .brand-name { left: 70px; top: 880px; font-size: 130px; color: var(--copper-bright); transform: rotate(-40deg); letter-spacing: 6px; }
  .label-abv { left: 880px; top: 840px; font-size: 72px; text-align: center; transform: rotate(-12deg); }
  .label-abv span { display: block; font-size: 44px; }
</style>
</head>
<body>
<main class="canvas">
  <section class="tin-wrap" aria-label="Unrolled gift tin label">
    <svg class="wrap-art" width="1080" height="1050" viewBox="0 0 1080 1050">
      <defs>
        <radialGradient id="topoTone" cx="0.5" cy="0.55" r="0.75">
          <stop offset="0" stop-color="#c2521c" stop-opacity="0.34"/>
          <stop offset="0.6" stop-color="#c2521c" stop-opacity="0.2"/>
          <stop offset="1" stop-color="#c2521c" stop-opacity="0.1"/>
        </radialGradient>
        <radialGradient id="skullTone" cx="0.5" cy="0.5" r="0.6">
          <stop offset="0" stop-color="#e8692a"/>
          <stop offset="1" stop-color="#7a2a0c" stop-opacity="0.85"/>
        </radialGradient>
      </defs>
      <rect class="topo-map" x="0" y="24" width="1080" height="1002" fill="url(#topoTone)" role="img" aria-label="Copper topographic contour map pattern across the tin"/>
      <g class="map-grid" stroke="var(--grid-line)" stroke-width="1.5">
        <line x1="135" y1="0" x2="135" y2="1050"/>
        <line x1="270" y1="0" x2="270" y2="1050"/>
        <line x1="405" y1="0" x2="405" y2="1050"/>
        <line x1="540" y1="0" x2="540" y2="1050"/>
        <line x1="675" y1="0" x2="675" y2="1050"/>
        <line x1="810" y1="0" x2="810" y2="1050"/>
        <line x1="945" y1="0" x2="945" y2="1050"/>
        <line x1="0" y1="220" x2="1080" y2="220"/>
        <line x1="0" y1="420" x2="1080" y2="420"/>
        <line x1="0" y1="620" x2="1080" y2="620"/>
        <line x1="0" y1="820" x2="1080" y2="820"/>
      </g>
      <rect class="rim-band" x="0" y="0" width="1080" height="24" fill="var(--copper-deep)" role="img" aria-label="Hatched copper rim band"/>
      <rect class="rim-band" x="0" y="1026" width="1080" height="24" fill="var(--copper-deep)" role="img" aria-label="Hatched copper rim band"/>
      <g class="rib" stroke="#000" stroke-width="10" opacity="0.6">
        <line x1="0" y1="350" x2="1080" y2="350"/>
        <line x1="0" y1="700" x2="1080" y2="700"/>
      </g>
      <ellipse class="skull-art" cx="710" cy="885" rx="110" ry="115" fill="url(#skullTone)" role="img" aria-label="Splattered copper skull illustration"/>
    </svg>
    <div class="label-text label-vodka">Vodka</div>
    <div class="label-text label-caution">Drink Cautiously</div>
    <div class="label-text label-since">Since<br>2017</div>
    <div class="label-text brand-name">Iron Drum</div>
    <div class="label-text label-abv">40%<span>Alcohol</span></div>
  </section>
</main>
</body>
</html>
```